Business card design for a dynamic IT consulting company

We need a business card design for a young firm, specialized in the Telecommunications/Consulting industry. The name of the company is Quindor and Partners Business Consulting Ltd. (Short name: Quindor and Partnes)
Quindor = solve read reverse, so we aim to be uncomplicated and solution-oriented. The small pipe in our logo is also related to the word solve. So we need a new business card design, which is simple, eye catching and something non traditional (I would probably prefer a square shaped design rather than a rectangle, but open for suggestions). Attached our logo.

Target Market(s)

Usually our customers are Tier1 Telecoms providers (Q-Netra, Palorix, etc) and their executives.

Industry/Entity Type

Business

Contact Information for Business Card

Name: Bence Tolnavari
Email: b.tolnavari@quindor.hu
Web: www.quindor.hu
Mobile: +36 30 518 2769
Title: Managing Director

Optional:
Company name: Quindor and Partners Ltd.
Address: 1087 Budapest, Tolvenka str. 28/C, Hungary

Font styles to use
Other font styles liked:
• helveticaneue_medium, Prime Regular are used now.

Colors

Designer to choose colors to be used in the design.

Requirements
Must have
• I would like to have a 2 sided design.
Nice to have
• I thought if we make the logo a bit bigger (without the company name), that could go to the back with the company name below. I though, if the pipe in the logo is somehow touchable on the business card, would be nice and unique.

```html
<!DOCTYPE html>
<html lang="en">
<head>
<meta charset="utf-8">
<title>Quindor and Partners – Business Card</title>
<link rel="stylesheet" href="https://fonts.googleapis.com/css2?family=Exo+2:wght@400;500&family=Arimo:wght@400&display=swap">
<style>
  :root {
    --page: #d9d4cc;
    --band-dark: #141416;
    --band-dark-2: #2a2a2e;
    --plum: #93306b;
    --blue: #1d6fb3;
    --ink: #1e1e22;
    --silver: #e6e8ec;
    --rose-brown: #a8706e;
    --address: #a39a98;
  }
  * { margin: 0; padding: 0; box-sizing: border-box; }
  html, body { width: 1200px; height: 970px; overflow: hidden; }
  body { background: var(--page); position: relative; }

  .card {
    position: absolute; left: 80px; top: 188px;
    width: 1040px; height: 593px;
    background: var(--band-dark);
    box-shadow: 0 14px 40px rgba(0,0,0,.28);
    overflow: hidden;
  }

  .card__header {
    position: absolute; left: 0; top: 0; width: 100%; height: 196px;
    background: linear-gradient(180deg, var(--band-dark-2), var(--band-dark) 70%);
  }
  .brand {
    position: absolute; left: 0; width: 100%; top: 52px;
    display: flex; justify-content: center; align-items: center; gap: 22px;
  }
  .brand__square { width: 34px; height: 34px; background: var(--silver); }
  .brand__name {
    font-family: "Exo 2", sans-serif; font-weight: 400;
    font-size: 64px; color: var(--silver); letter-spacing: 1px;
  }

  .card__rule {
    position: absolute; left: 0; width: 100%; height: 4px;
    background: linear-gradient(90deg, var(--plum) 0 50%, var(--blue) 50% 100%);
  }
  .card__rule--top { top: 198px; }
  .card__rule--bottom { top: 466px; }

  .card__body {
    position: absolute; left: 0; top: 202px; width: 100%; height: 264px;
    background:
      radial-gradient(ellipse at 50% 95%, rgba(236,150,170,.55), transparent 45%),
      radial-gradient(ellipse at 90% 40%, rgba(160,195,230,.6), transparent 50%),
      linear-gradient(90deg, #e9ddd0, #f4f1ee 30%, #eef0f3 60%, #cfd9e4);
  }
  .body-brand {
    position: absolute; left: 150px; top: 106px;
    display: flex; align-items: center; gap: 16px;
  }
  .body-brand__square { width: 40px; height: 40px; background: var(--plum); }
  .body-brand__name {
    font-family: "Exo 2", sans-serif; font-weight: 500;
    font-size: 44px; color: var(--blue);
  }
  .divider {
    position: absolute; left: 465px; top: 48px; width: 2px; height: 170px;
    background: var(--plum);
  }

  .contact { position: absolute; left: 529px; top: 40px; }
  .contact__name {
    font-family: "Exo 2", sans-serif; font-weight: 500;
    font-size: 35px; color: var(--ink); line-height: 40px;
  }
  .contact__title {
    font-family: "Arimo", sans-serif; font-size: 24px;
    color: var(--plum); line-height: 28px;
  }
  .contact__list { list-style: none; margin-top: 20px; }
  .contact__item {
    display: flex; align-items: center; gap: 14px;
    font-family: "Arimo", sans-serif; font-size: 24px;
    color: var(--ink); height: 30px;
  }
  .contact__icon { width: 24px; height: 24px; flex: none; }

  .card__footer {
    position: absolute; left: 0; top: 470px; width: 100%; height: 123px;
    background: linear-gradient(180deg, var(--band-dark-2), var(--band-dark));
    text-align: center; padding-top: 30px;
  }
  .footer__company {
    font-family: "Exo 2", sans-serif; font-size: 29px;
    color: var(--rose-brown); letter-spacing: 1px; line-height: 34px;
  }
  .footer__address {
    font-family: "Arimo", sans-serif; font-size: 24px;
    color: var(--address); line-height: 30px;
  }
</style>
</head>
<body>
  <div class="card">
    <header class="card__header">
      <div class="brand">
        <span class="brand__square"></span>
        <span class="brand__name">Quindor &amp; Partners</span>
      </div>
    </header>

    <div class="card__rule card__rule--top"></div>

    <section class="card__body">
      <div class="body-brand">
        <span class="body-brand__square"></span>
        <span class="body-brand__name">Quindor</span>
      </div>
      <div class="divider"></div>

      <div class="contact">
        <div class="contact__name">Bence Tolnavari</div>
        <div class="contact__title">Managing Director</div>
        <ul class="contact__list">
          <li class="contact__item">
            <svg class="contact__icon" viewBox="0 0 24 24" aria-hidden="true">
              <rect width="24" height="24" fill="#93306b"/>
              <rect x="7" y="3.5" width="10" height="17" rx="1.5" fill="none" stroke="#fff" stroke-width="2"/>
              <rect x="10" y="16.5" width="4" height="1.6" fill="#fff"/>
            </svg>
            +36 30 518 2769
          </li>
          <li class="contact__item">
            <svg class="contact__icon" viewBox="0 0 24 24" aria-hidden="true">
              <rect width="24" height="24" fill="#2b2b2f"/>
              <rect x="4" y="6.5" width="16" height="11" fill="none" stroke="#fff" stroke-width="1.6"/>
              <path d="M4 6.5 L12 13 L20 6.5 M4 17.5 L10 11.5 M20 17.5 L14 11.5" fill="none" stroke="#fff" stroke-width="1.4"/>
            </svg>
            b.tolnavari@quindor.hu
          </li>
          <li class="contact__item">
            <svg class="contact__icon" viewBox="0 0 24 24" aria-hidden="true">
              <rect width="24" height="24" fill="#1d6fb3"/>
              <circle cx="12" cy="12" r="7.5" fill="none" stroke="#fff" stroke-width="1.4"/>
              <ellipse cx="12" cy="12" rx="3.2" ry="7.5" fill="none" stroke="#fff" stroke-width="1.2"/>
              <path d="M4.5 12 H19.5 M6 8 H18 M6 16 H18" stroke="#fff" stroke-width="1.1"/>
            </svg>
            www.quindor.hu
          </li>
        </ul>
      </div>
    </section>

    <div class="card__rule card__rule--bottom"></div>

    <footer class="card__footer">
      <div class="footer__company">Quindor and Partners Ltd.</div>
      <div class="footer__address">1087 Budapest, Tolvenka str. 28/C, Hungary</div>
    </footer>
  </div>
</body>
</html>
```